Create Product Deck for Organic Beard Oil Brand

We need a product deck to showcase our beard oil collection to potential buyers from department stores, barbershops/salons and wholesale buyers. Attached is a perfect example of the style and layout we want for our product deck.The info regarding the brand should include the following:Company BioPerformance Month OverviewGlobal Reach ShowcaseThe info for each product should include the following:Product NameSKU and/or UPCProduct DescriptionCase SizeWholesale PricingRetail PricingIngredients

Target Market(s)

Men with beards in the U.S.

Women who are married or in a relationship with a bearded man.

Ethnicity: African-American/Multicutural/White

Ages: 24 - 45

Middle Class / Fathers / Married / Dating / Single

Industry/Entity Type

Hair And Beauty

Font styles to use
Sans Serif
Other font styles liked:
• ITC Franklin Gothic

Colors
acd036
0692cd
f04a50

Requirements
Must have
• Must be bright, colorful and showcase each of the products highlighting their particular scents.
• List of our products to be shown in product deck:
• Mango Ginger Beard Oil
• Warm Hazel Beard Oil
• Crown Of The Hour Beard Oil
• Golden Otter Beard Oil
• Evening Tide Beard Oil
• Heritage Mix Beard Oil
• Images for each of these products have been included as well.
Nice to have
• Surprise me by showing off your personal flash and flare. Do not let our color preferences restrict you from this.
Should not have
• No "bro culture" copy.
• No woodsmen/lumberjack styles like other beard brands have.

```html
<!DOCTYPE html>
<html lang="en">
<head>
<meta charset="utf-8">
<title>Digital Marketing Takeover – Holiday Season Performance Overview</title>
<link rel="stylesheet" href="https://fonts.googleapis.com/css2?family=Libre+Franklin:wght@400;500;600;700;800;900&display=swap">
<style>
  :root {
    --green-light: #95c94a;
    --green-mid: #7fb834;
    --green-deep: #65a027;
    --band-green: #a3cf6a;
    --white: #ffffff;
    --ink: #333333;
    --ink-soft: #777777;
    --star: #f2b01e;
    --strip: #f3f3f3;
    --bezel: #1c1c1c;
    --bezel-edge: #b9b9b9;
    --base-light: #e6e6e6;
    --base-dark: #9a9a9a;
  }
  * { box-sizing: border-box; margin: 0; padding: 0; }
  html, body { width: 1200px; height: 927px; overflow: hidden; }
  body { font-family: "Libre Franklin", Arial, sans-serif; }

  .slide {
    position: relative;
    width: 1200px; height: 927px;
    overflow: hidden;
    background:
      radial-gradient(ellipse 420px 300px at 1120px 80px, rgba(255,255,255,.16), rgba(255,255,255,0) 70%),
      radial-gradient(ellipse 700px 560px at 600px 470px, var(--green-light), var(--green-mid) 60%, var(--green-deep) 100%);
    color: var(--white);
  }

  .headline { position: absolute; left: 80px; top: 98px; }
  .headline h1 {
    font-weight: 900; font-size: 50px; line-height: 1; letter-spacing: 0.5px;
    text-transform: uppercase;
  }
  .headline h2 {
    margin-top: 12px;
    font-weight: 800; font-size: 25px; line-height: 1; letter-spacing: 0.6px;
    text-transform: uppercase;
  }

  .stat {
    position: absolute; width: 240px; text-align: center;
  }
  .stat svg { display: block; margin: 0 auto; fill: var(--white); }
  .stat .value { font-weight: 900; font-size: 70px; line-height: 1; letter-spacing: -1px; }
  .stat .label { font-weight: 500; font-size: 24px; line-height: 1; margin-top: 4px; }

  .stat-orders { left: 26px; top: 290px; }
  .stat-impressions { left: 26px; top: 522px; }
  .stat-reached { left: 923px; top: 304px; }
  .stat-emails { left: 923px; top: 520px; }

  .stat-visitors { position: absolute; left: 460px; top: 770px; width: 300px; }
  .stat-visitors .row { display: flex; align-items: center; gap: 8px; }
  .stat-visitors svg { fill: var(--white); }
  .stat-visitors .value { font-weight: 900; font-size: 76px; line-height: 1; letter-spacing: -1px; }
  .stat-visitors .label { font-weight: 500; font-size: 24px; margin-top: 12px; margin-left: 6px; white-space: nowrap; }

  /* laptop */
  .laptop-lid {
    position: absolute; left: 295px; top: 281px; width: 611px; height: 406px;
    background: var(--bezel); border-radius: 16px 16px 0 0;
    border: 2px solid var(--bezel-edge); border-bottom: none;
  }
  .laptop-camera {
    position: absolute; left: 598px; top: 292px; width: 5px; height: 5px;
    border-radius: 50%; background: #3a3a3a;
  }
  .laptop-base {
    position: absolute; left: 190px; top: 684px; width: 820px; height: 34px;
    background: linear-gradient(var(--base-light), #cfcfcf 55%, var(--base-dark));
    border-radius: 3px 3px 40px 40px / 3px 3px 14px 14px;
    box-shadow: 0 6px 10px rgba(0,0,0,.18);
  }
  .laptop-notch {
    position: absolute; left: 536px; top: 684px; width: 128px; height: 11px;
    background: linear-gradient(#bdbdbd, #d9d9d9); border-radius: 0 0 8px 8px;
  }

  .screen {
    position: absolute; left: 322px; top: 309px; width: 556px; height: 351px;
    background: var(--white); overflow: hidden; color: var(--ink);
  }
  .promise-band {
    height: 88px; background: var(--band-green); display: flex;
    padding: 20px 14px 0; gap: 16px; color: var(--white);
  }
  .promise { flex: 1; text-align: center; }
  .promise svg { display: block; margin: 0 auto 5px; fill: var(--white); }
  .promise h3 { font-size: 5.5px; font-weight: 600; margin-bottom: 5px; }
  .promise p { font-size: 4px; line-height: 1.5; }

  .favorites-title {
    text-align: center; font-size: 5px; letter-spacing: 0.6px; text-transform: uppercase;
    color: var(--ink-soft); margin-top: 21px;
  }
  .product-row { position: absolute; left: 0; top: 118px; width: 556px; }
  .product {
    position: absolute; width: 128px; text-align: center;
  }
  .product .photo { width: 120px; height: 125px; margin: 0 auto; border-radius: 4px; }
  .product h4 { font-size: 4.2px; font-weight: 500; margin-top: 7px; text-transform: uppercase; letter-spacing: 0.2px; }
  .product .price { font-size: 4.2px; color: var(--ink-soft); margin-top: 3px; }
  .product .stars { font-size: 5px; color: var(--star); line-height: 1; margin-top: 1px; letter-spacing: 0.5px; }
  .product .reviews { font-size: 3.8px; color: var(--ink-soft); }

  .photo-lemon { background: radial-gradient(circle at 50% 55%, #8a5a22 0 14%, #f4c542 30%, #f0a21c 55%, #9bbf5a 80%, var(--white) 100%); }
  .photo-coconut { background: radial-gradient(circle at 50% 55%, #8a5a22 0 14%, #d9d0c2 34%, #8dc63f 60%, var(--white) 90%); }
  .photo-orange { background: radial-gradient(circle at 50% 55%, #8a5a22 0 14%, #f39a1e 38%, #e3d2bd 65%, var(--white) 92%); }
  .photo-almond { background: radial-gradient(circle at 50% 55%, #8a5a22 0 14%, #b5642f 40%, #c98150 65%, var(--white) 92%); }

  .review-strip {
    position: absolute; left: 0; top: 293px; width: 556px; height: 38px;
    background: var(--strip); display: flex; padding: 7px 20px 0;
  }
  .review { flex: 1; text-align: center; }
  .review .stars { font-size: 5px; color: var(--star); letter-spacing: 0.5px; line-height: 1; }
  .review q { display: block; font-size: 4.6px; font-weight: 700; margin-top: 3px; quotes: "\201C" "\201D"; }
  .review cite { display: block; font-size: 4px; font-style: normal; color: var(--ink-soft); margin-top: 1px; }
  .footer-block {
    position: absolute; left: 0; top: 331px; width: 334px; height: 20px; background: #e4e4e4;
  }
</style>
</head>
<body>
<main class="slide">

  <header class="headline">
    <h1>Digital Marketing Takeover</h1>
    <h2>Holiday Season Performance Overview</h2>
  </header>

  <section class="stat stat-orders">
    <svg width="48" height="46" viewBox="0 0 48 46" aria-hidden="true">
      <path d="M14 17 L24 3 L34 17" fill="none" stroke="#fff" stroke-width="3"/>
      <rect x="2" y="16" width="44" height="6" rx="1"/>
      <path d="M5 24 H43 L39 44 H9 Z"/>
      <g fill="#7fb834"><rect x="13" y="27" width="3" height="13"/><rect x="20" y="27" width="3" height="13"/><rect x="27" y="27" width="3" height="13"/><rect x="34" y="27" width="3" height="13"/></g>
    </svg>
    <div class="value">10K</div>
    <div class="label">Website Orders</div>
  </section>

  <section class="stat stat-impressions">
    <svg width="84" height="34" viewBox="0 0 84 34" aria-hidden="true">
      <path d="M2 17 C18 -4 66 -4 82 17 C66 38 18 38 2 17 Z M42 6 A11 11 0 1 0 42 28 A11 11 0 1 0 42 6 Z" fill-rule="evenodd"/>
      <path d="M8 17 C22 2 62 2 76 17 C62 32 22 32 8 17 Z" fill="#7fb834"/>
      <circle cx="42" cy="17" r="11"/>
    </svg>
    <div class="value" style="margin-top:8px">20K</div>
    <div class="label">Impressions</div>
  </section>

  <section class="stat stat-reached">
    <svg width="68" height="38" viewBox="0 0 68 38" aria-hidden="true">
      <circle cx="14" cy="10" r="6"/><path d="M2 38 V26 A8 8 0 0 1 10 18 H18 A8 8 0 0 1 26 26 V38 Z"/>
      <circle cx="54" cy="10" r="6"/><path d="M42 38 V26 A8 8 0 0 1 50 18 H58 A8 8 0 0 1 66 26 V38 Z"/>
      <circle cx="34" cy="8" r="7"/><path d="M21 38 V24 A9 9 0 0 1 30 16 H38 A9 9 0 0 1 47 24 V38 Z"/>
    </svg>
    <div class="value" style="margin-top:8px">12K</div>
    <div class="label">People Reached</div>
  </section>

  <section class="stat stat-emails">
    <svg width="58" height="38" viewBox="0 0 58 38" aria-hidden="true">
      <rect x="1" y="1" width="56" height="36" fill="none" stroke="#fff" stroke-width="2.5"/>
      <path d="M1 1 L29 22 L57 1" fill="none" stroke="#fff" stroke-width="2.5"/>
      <path d="M1 37 L22 17 M57 37 L36 17" fill="none" stroke="#fff" stroke-width="2.5"/>
    </svg>
    <div class="value" style="margin-top:8px">50K</div>
    <div class="label">Emails Collected</div>
  </section>

  <div class="laptop-lid"></div>
  <div class="laptop-camera"></div>

  <section class="screen">
    <div class="promise-band">
      <div class="promise">
        <svg width="12" height="12" viewBox="0 0 12 12" aria-hidden="true"><rect x="0" y="5" width="3" height="7"/><path d="M4 5 L7 0 C8.5 0 8.5 2 8 4 H12 V7 L10 12 H4 Z"/></svg>
        <h3>Satisfaction Guaranteed</h3>
        <p>Our customers love our oils, and if you are not happy<br>we will make it right.</p>
      </div>
      <div class="promise">
        <svg width="12" height="12" viewBox="0 0 12 12" aria-hidden="true"><circle cx="3" cy="4" r="1.5"/><circle cx="5.3" cy="1.8" r="1.5"/><circle cx="8" cy="1.8" r="1.5"/><circle cx="10" cy="4" r="1.5"/><ellipse cx="6.5" cy="8.5" rx="3.2" ry="2.8"/></svg>
        <h3>Cruelty Free</h3>
        <p>Every blend is tested on us, never on animals,<br>using ethically sourced ingredients.</p>
      </div>
      <div class="promise">
        <svg width="14" height="12" viewBox="0 0 14 12" aria-hidden="true"><rect x="0" y="2" width="8" height="7"/><path d="M8 4 H11 L14 7 V9 H8 Z"/><circle cx="3" cy="10" r="1.6"/><circle cx="11" cy="10" r="1.6"/></svg>
        <h3>Fast Delivery</h3>
        <p>All orders ship within 24 to 48 hours,<br>tracked from our door to yours.</p>
      </div>
    </div>

    <p class="favorites-title">Customer Favorites</p>

    <div class="product-row">
      <article class="product" style="left:4px">
        <div class="photo photo-lemon" role="img" aria-label="Bottle of Crown Of The Hour Beard Oil with lemons and sea buckthorn"></div>
        <h4>Crown Of The Hour Beard Oil</h4>
        <div class="price">$ 19.95</div>
      </article>
      <article class="product" style="left:138px">
        <div class="photo photo-coconut" role="img" aria-label="Bottle of Mango Ginger Beard Oil with coconut and lime"></div>
        <h4>Mango Ginger Beard Oil</h4>
        <div class="price">$ 19.95</div>
        <div class="stars">★★★★★</div>
        <div class="reviews">12 reviews</div>
      </article>
      <article class="product" style="left:274px">
        <div class="photo photo-orange" role="img" aria-label="Bottle of Evening Tide Beard Oil with orange and sandalwood"></div>
        <h4>Evening Tide Beard Oil</h4>
        <div class="price">$ 19.95</div>
        <div class="stars">★★★★★</div>
        <div class="reviews">1 review</div>
      </article>
      <article class="product" style="left:402px">
        <div class="photo photo-almond" role="img" aria-label="Bottle of Warm Hazel Beard Oil with almonds"></div>
        <h4>Warm Hazel Beard Oil | Fragrance Free</h4>
        <div class="price">$ 19.95</div>
        <div class="stars">★★★★★</div>
        <div class="reviews">6 reviews</div>
      </article>
    </div>

    <div class="review-strip">
      <div class="review">
        <div class="stars">★★★★★</div>
        <q>The Mango Ginger beard oil is absolutely fantastic</q>
        <cite>-Dalen Pruitt</cite>
      </div>
      <div class="review">
        <div class="stars">★★★★★</div>
        <q>THIS IS A GREAT PRODUCT!!!</q>
        <cite>-Noel Ashby</cite>
      </div>
      <div class="review">
        <div class="stars">★★★★★</div>
        <q>Don't waste your money on other brands</q>
        <cite>-Reid Calloway</cite>
      </div>
    </div>
    <div class="footer-block"></div>
  </section>

  <div class="laptop-base"></div>
  <div class="laptop-notch"></div>

  <section class="stat-visitors">
    <div class="row">
      <svg width="68" height="54" viewBox="0 0 68 54" aria-hidden="true">
        <rect x="2" y="2" width="64" height="40" rx="2" fill="none" stroke="#fff" stroke-width="4"/>
        <rect x="29" y="42" width="10" height="7"/>
        <rect x="16" y="49" width="36" height="4"/>
        <circle cx="26" cy="17" r="5"/><path d="M16 36 V30 A6 6 0 0 1 22 24 H30 A6 6 0 0 1 36 30 V36 Z"/>
        <circle cx="43" cy="15" r="5"/><path d="M36 24 A6 6 0 0 1 39 22 H47 A6 6 0 0 1 53 28 V36 H39 V30 Z"/>
      </svg>
      <div class="value">500K</div>
    </div>
    <div class="label">Overall Website Visitors</div>
  </section>

</main>
</body>
</html>
```